Help our Sugar Loom find our winning design! We're looking for a business card....

We’re a Sugar Loom in NY specializing in custom-made cakes and unique desserts.
Our cakes combine flavor and art, each designed to match customer’s special event and theme.
We’d like a unique business card with a clean design that will combine French chic and artistic look & feel.
We’d like to differentiate ourselves from standard bakeries, please don’t offer cupcake images :-)
Our logo is peach-pink and brown and we’d love to use these colors ( . Another color that can be added is gold - or feel free to suggest!

Target Market(s)

Women, ages 25-55

Industry/Entity Type

Boutique

Contact Information for Business Card

Text on card:
Logo
Sugar Loom by Dana Welch

www.sugarloomsweets.com
hello@sugarloom.com
(516) 555-0147
F – sugarloomnyc
IG - sugarloom_ny

Font styles to use
Sans Serif
Script

Requirements
Must have
• Logo
• Clean look
• French chic and artistic look & feel.
Nice to have
• Damask pattern
Should not have
• Cupcake images

```html
<!DOCTYPE html>
<html lang="en">
<head>
<meta charset="utf-8">
<title>Sugar Loom — Business Card</title>
<link rel="stylesheet" href="https://fonts.googleapis.com/css2?family=Open+Sans:wght@400&family=Pinyon+Script&display=swap">
<style>
  :root {
    --backdrop: #bdbdbd;
    --card-light: #ffffff;
    --card-dark: #221416;
    --rose: #e2a59d;
    --rose-soft: rgba(226, 165, 157, 0.55);
    --cocoa: #2a1c1e;
    --cream: #f6ece8;
  }
  * { box-sizing: border-box; margin: 0; padding: 0; }
  html, body { width: 1200px; height: 852px; overflow: hidden; }
  body {
    background: var(--backdrop);
    font-family: "Open Sans", Arial, sans-serif;
    position: relative;
  }
  .card {
    position: absolute;
    width: 500px;
    height: 286px;
    border-radius: 22px;
    box-shadow: 0 6px 18px rgba(0, 0, 0, 0.22);
    overflow: hidden;
  }
  .card-front {
    left: 130px; top: 110px;
    background: var(--card-light);
    display: flex; align-items: center; justify-content: center;
  }
  .card-back {
    left: 570px; top: 456px;
    background: var(--card-dark);
  }
  .brand-name {
    font-family: "Pinyon Script", cursive;
    font-size: 64px;
    line-height: 1;
    color: var(--cocoa);
    display: flex; align-items: center; gap: 14px;
  }
  .brand-dot {
    width: 12px; height: 12px; border-radius: 50%;
    background: var(--rose);
  }
  .card-back .brand-name {
    position: absolute;
    left: 30px; top: 118px;
    font-size: 46px;
    color: var(--cream);
  }
  .divider {
    position: absolute;
    left: 262px; top: 40px;
    width: 1px; height: 200px;
    background: linear-gradient(to bottom, transparent, var(--rose-soft), transparent);
    transform: rotate(-8deg);
  }
  .owner {
    position: absolute;
    left: 300px; top: 48px;
    color: var(--cream);
  }
  .owner-line { font-size: 14px; letter-spacing: 0.2px; }
  .owner-name {
    font-family: "Pinyon Script", cursive;
    font-size: 30px;
    line-height: 1.1;
  }
  .contacts {
    position: absolute;
    left: 300px; top: 148px;
    list-style: none;
    color: var(--rose);
    font-size: 11.5px;
    line-height: 17px;
  }
  .contacts li { display: flex; align-items: center; gap: 9px; }
  .contacts svg { width: 11px; height: 11px; flex: none; }
  .social-mark {
    width: 10px; height: 10px; flex: none;
    background: var(--rose);
    border-radius: 2px;
  }
</style>
</head>
<body>
  <section class="card card-front" aria-label="Card front">
    <div class="brand-name"><span class="brand-dot"></span>Sugar Loom</div>
  </section>

  <section class="card card-back" aria-label="Card back">
    <div class="brand-name">Sugar Loom</div>
    <div class="divider"></div>

    <div class="owner">
      <p class="owner-line">Sugar Loom by</p>
      <p class="owner-name">Dana Welch</p>
    </div>

    <ul class="contacts">
      <li>
        <svg viewBox="0 0 12 12" aria-hidden="true"><path fill="#e2a59d" d="M2 1h2.5l1 3-1.5 1a6 6 0 0 0 3 3l1-1.5 3 1V10a1.5 1.5 0 0 1-1.5 1.5A9 9 0 0 1 .5 2.5 1.5 1.5 0 0 1 2 1z"/></svg>
        (516) 555-0147
      </li>
      <li>
        <svg viewBox="0 0 12 12" aria-hidden="true"><rect x="0.5" y="2.5" width="11" height="7" fill="none" stroke="#e2a59d"/><path d="M0.5 2.5 6 7l5.5-4.5" fill="none" stroke="#e2a59d"/></svg>
        hello@sugarloom.com
      </li>
      <li>
        <svg viewBox="0 0 12 12" aria-hidden="true"><circle cx="6" cy="6" r="5.3" fill="none" stroke="#e2a59d"/><ellipse cx="6" cy="6" rx="2.3" ry="5.3" fill="none" stroke="#e2a59d"/><path d="M0.7 6h10.6" stroke="#e2a59d"/></svg>
        www.sugarloomsweets.com
      </li>
      <li><span class="social-mark"></span>sugarloomnyc</li>
      <li><span class="social-mark"></span>sugarloom_ny</li>
    </ul>
  </section>
</body>
</html>
```